Business card design for new eCommerce site focusing on integrity and strong businsess tactics

We need a business card that will stand out and be memorable. Something with color that matches our company logo colors. Think high end version of Pactivo. There are 2 logos provided. The parent company is called Amber Ledge Partners and we are presenting a new and very exciting eCommerce site called BrightHarborTrade.example.

Target Market(s)

Our target markets are in the Activities, Food and Beverage, Health and Beauty

Industry/Entity Type

Marketing

Contact Information for Business Card

We have 4 members that need cards...I will provide all info to the winner of the design contest
Business Address is
4870 West 63rd Avenue, Suite C207
Phoenix AZ 85731

Font styles to use
Serif
Sans Serif

Colors

Designer to choose colors to be used in the design.

Requirements
Must have
• The card must be memorable...should be unique in design but must exude integrity and be playful .
• I have provided several colors or our parent company...please feel free to use which ever
Nice to have
• I will leave this up to you. Feel free to use other images of your choosing that wraps around our client.....Activities, Dining, Health, Beauty
Should not have
• just dont be boring

```html
<!DOCTYPE html>
<html lang="en">
<head>
<meta charset="utf-8">
<title>Amber Ledge Partners – Business Card</title>
<link href="https://fonts.googleapis.com/css2?family=Montserrat:wght@400;500;700&display=swap" rel="stylesheet">
<style>
  :root{
    --bg:#d6d6d6;
    --blue:#2a78b3;
    --blue-deep:#226aa2;
    --green:#8cc63f;
    --ink:#4a4a4a;
    --white:#ffffff;
  }
  *{box-sizing:border-box;margin:0;padding:0}
  html,body{width:1200px;height:800px;overflow:hidden}
  body{background:var(--bg);font-family:"Montserrat",Arial,sans-serif;position:relative}

  .card{position:absolute;left:300px;width:600px;height:343px;overflow:hidden;
        box-shadow:0 6px 18px rgba(0,0,0,.18)}
  .card--front{top:30px;background:var(--white)}
  .card--back{top:420px;background:var(--blue)}

  /* front */
  .front-swoosh{position:absolute;inset:0}
  .brand{position:absolute;left:48px;top:122px;width:230px;display:flex;align-items:center;gap:12px}
  .brand__dot{width:22px;height:22px;border-radius:50%;background:var(--green);flex:none}
  .brand__name{color:var(--green);font-weight:700;font-size:25px;line-height:1.15}

  .person{position:absolute;left:330px;top:40px;padding-left:14px;border-left:3px solid var(--blue)}
  .person__name{color:var(--blue);font-weight:700;font-size:16px;line-height:1.2}
  .person__role{color:var(--ink);font-size:13px;line-height:1.3}

  .contact{position:absolute;left:330px;top:100px;padding-left:14px;border-left:2px solid var(--green);list-style:none}
  .contact li{display:flex;align-items:center;gap:8px;color:var(--ink);font-size:11.5px;line-height:19px}
  .contact svg{width:11px;height:11px;flex:none}
  .contact .address{padding-left:19px;display:block}

  /* back */
  .back-pattern{position:absolute;inset:0;background:radial-gradient(circle at 30% 40%,var(--blue) 0%,var(--blue-deep) 100%)}
  .back-brand{position:absolute;left:0;right:0;top:118px;display:flex;justify-content:center;align-items:center;gap:16px}
  .back-brand__dot{width:40px;height:40px;border-radius:50%;background:var(--white);flex:none}
  .back-brand__name{color:var(--white);font-weight:700;font-size:30px;line-height:1.1}
  .back-brand__tagline{color:var(--white);font-size:13px;letter-spacing:.5px;margin-top:4px}
  .back-web{position:absolute;left:0;right:0;top:258px;text-align:center;color:var(--white);font-size:12px;letter-spacing:1px}
</style>
</head>
<body>

<section class="card card--front" aria-label="Card front">
  <svg class="front-swoosh" viewBox="0 0 600 343" preserveAspectRatio="none" aria-hidden="true">
    <path d="M0,343 L0,324 C220,308 460,284 600,232 L600,343 Z" fill="var(--blue)"/>
    <path d="M280,304 C420,290 530,262 600,212 L600,232 C520,268 420,294 280,304 Z" fill="var(--green)"/>
  </svg>

  <div class="brand">
    <span class="brand__dot"></span>
    <span class="brand__name">Amber Ledge Partners</span>
  </div>

  <div class="person">
    <p class="person__name">Daniel Reyes</p>
    <p class="person__role">Founder</p>
  </div>

  <ul class="contact">
    <li>
      <svg viewBox="0 0 12 12"><rect x="3" y="0.5" width="6" height="11" rx="1" fill="none" stroke="var(--blue)" stroke-width="1.2"/></svg>
      0426 739 418
    </li>
    <li>
      <svg viewBox="0 0 12 12"><rect x="0.5" y="2" width="11" height="8" fill="var(--blue)"/><path d="M0.5,2 L6,6.5 L11.5,2" fill="none" stroke="#fff" stroke-width="1"/></svg>
      info@brightharbortrade.example
    </li>
    <li>
      <svg viewBox="0 0 12 12"><circle cx="5" cy="5" r="3.6" fill="none" stroke="var(--blue)" stroke-width="1.6"/><path d="M7.6,7.6 L11,11" stroke="var(--blue)" stroke-width="1.8"/></svg>
      www.brightharbortrade.example
    </li>
    <li class="address">4870 West 63rd Avenue,<br>Suite C207 Phoenix AZ 85731</li>
  </ul>
</section>

<section class="card card--back" aria-label="Card back">
  <div class="back-pattern" role="img" aria-label="Soft tone-on-tone flower pattern in blue"></div>
  <div class="back-brand">
    <span class="back-brand__dot"></span>
    <div>
      <p class="back-brand__name">BrightHarborTrade.example</p>
      <p class="back-brand__tagline">Activities-Dining-Health-Beauty</p>
    </div>
  </div>
  <p class="back-web">www.amberledgepartners.example</p>
</section>

</body>
</html>
```